Moravel Aesthetic Doctor

I require an elegant, luxurious looking business card for my aesthetic business. I am a doctor and that will set me aside from competitors. I am planning to provide home and spa based treatments to clients with high expectations. I have attached my logo.

```html
<!DOCTYPE html>
<html lang="en">
<head>
<meta charset="utf-8">
<title>Moravel Aesthetic Doctor – Business Card</title>
<link href="https://fonts.googleapis.com/css2?family=Marcellus&family=Open+Sans:wght@400;600&display=swap" rel="stylesheet">
<style>
  :root {
    --page-bg: #ece9e4;
    --card-top: #2384cc;
    --card-bottom: #1568b3;
    --white: #ffffff;
    --accent: #4fc3f0;
    --pale: #cfe6f7;
    --wave-a: rgba(255,255,255,0.16);
    --wave-b: rgba(120,200,240,0.22);
  }
  * { margin: 0; padding: 0; box-sizing: border-box; }
  html, body { width: 1200px; height: 1136px; overflow: hidden; }
  body {
    background: var(--page-bg);
    font-family: "Open Sans", Arial, sans-serif;
    display: flex;
    flex-direction: column;
    align-items: center;
    justify-content: space-evenly;
  }
  .card {
    position: relative;
    width: 860px;
    height: 491px;
    border-radius: 4px;
    background: radial-gradient(ellipse at 40% 40%, var(--card-top), var(--card-bottom) 85%);
    box-shadow: 0 14px 30px rgba(0,0,0,0.25);
    overflow: hidden;
    color: var(--white);
  }

  /* Back: contact details */
  .back .wave-art {
    position: absolute;
    left: 0; bottom: 0;
    width: 420px; height: 300px;
    border-top-right-radius: 100% 90%;
    background: linear-gradient(160deg, var(--wave-a), var(--wave-b) 60%, rgba(255,255,255,0.05));
  }
  .back .details {
    position: absolute;
    left: 330px; top: 78px;
  }
  .name {
    font-size: 34px;
    font-weight: 400;
    letter-spacing: 0.3px;
  }
  .name .credentials {
    font-size: 13px;
    color: var(--accent);
    margin-left: 6px;
    letter-spacing: 0.5px;
  }
  .diploma { font-size: 20px; margin-top: 2px; }
  .divider {
    width: 44px; height: 3px;
    background: var(--accent);
    margin: 20px 0 14px;
  }
  .contact-list { list-style: none; font-size: 19px; line-height: 31px; }
  .contact-list li { display: flex; align-items: center; gap: 14px; }
  .contact-list svg { width: 17px; height: 17px; fill: var(--accent); flex: none; }
  .social-row { display: flex; gap: 10px; margin: 8px 0 12px; }
  .social-row span {
    width: 17px; height: 17px; border-radius: 50%;
    background: var(--accent);
  }
  .services { font-size: 20px; line-height: 30px; }

  /* Front: brand */
  .front .brand {
    position: absolute;
    left: 120px; top: 150px;
    display: flex; align-items: center; gap: 26px;
  }
  .brand-ring {
    width: 150px; height: 150px;
    border: 4px solid var(--white);
    border-radius: 50%;
    flex: none;
  }
  .brand-name {
    font-family: "Marcellus", Georgia, serif;
    color: var(--white);
    line-height: 1;
  }
  .brand-name .word { display: block; font-size: 104px; letter-spacing: 6px; }
  .brand-name .sub { display: block; font-size: 34px; letter-spacing: 3px; margin-top: 6px; }
  .tagline {
    position: absolute;
    left: 400px; top: 372px;
    font-size: 24px;
    letter-spacing: 0.6px;
    color: var(--pale);
  }
</style>
</head>
<body>
  <section class="card back">
    <div class="wave-art" role="img" aria-label="Faint flowing hair and profile emblem decoration"></div>
    <div class="details">
      <h1 class="name">Dr Elise Varden<span class="credentials">MRCPCH MD</span></h1>
      <p class="diploma">Australasian Diploma of Aesthetic Medicine</p>
      <div class="divider"></div>
      <ul class="contact-list">
        <li><svg viewBox="0 0 24 24"><path d="M6.6 10.8a15 15 0 0 0 6.6 6.6l2.2-2.2c.3-.3.7-.4 1-.2 1.1.4 2.3.6 3.6.6.6 0 1 .4 1 1V20c0 .6-.4 1-1 1A17 17 0 0 1 3 4c0-.6.4-1 1-1h3.5c.6 0 1 .4 1 1 0 1.3.2 2.5.6 3.6.1.3 0 .7-.2 1z"/></svg>0800 555 014</li>
        <li><svg viewBox="0 0 24 24"><path d="M2 5h20v14H2zm2 2v.5l8 5 8-5V7zm0 2.8V17h16V9.8l-8 5z"/></svg>elise@moravel.co.nz</li>
        <li><svg viewBox="0 0 24 24"><path d="M12 2a10 10 0 1 0 0 20 10 10 0 0 0 0-20zm7.9 9h-3.9a15 15 0 0 0-1.4-6.3A8 8 0 0 1 19.9 11zM12 4c.9 1.2 1.8 3.6 2 7h-4c.2-3.4 1.1-5.8 2-7zM9.4 4.7A15 15 0 0 0 8 11H4.1a8 8 0 0 1 5.3-6.3zM4.1 13H8a15 15 0 0 0 1.4 6.3A8 8 0 0 1 4.1 13zM12 20c-.9-1.2-1.8-3.6-2-7h4c-.2 3.4-1.1 5.8-2 7zm2.6-.7A15 15 0 0 0 16 13h3.9a8 8 0 0 1-5.3 6.3z"/></svg>www.moravel.co.nz</li>
      </ul>
      <div class="social-row"><span></span><span></span></div>
      <p class="services">Dermal injectables - Plasma facials<br>Microneedling - Skin boosters<br>Excessive sweating</p>
    </div>
  </section>

  <section class="card front">
    <div class="brand">
      <div class="brand-ring"></div>
      <p class="brand-name"><span class="word">MORAVEL</span><span class="sub">AESTHETIC DOCTOR</span></p>
    </div>
    <p class="tagline">Home and Spa Based Treatments</p>
  </section>
</body>
</html>
```